Business Card Design Project

I have established a company called "Corvella" which is a business specialising in psychotherapy/counselling , predominantly for anxiety & depression.

My name is Nel....hence, the Corvella link. However, Corvella was also chosen for its reference to green shoots of growth/recovery.

Corvella is to be "upmarket" and highly professional. I'm keen for the style and colours to reflect this.....taupe/grey with navy/black script, for example.....NO primary colours.

My name needs to be on the card and my mobile number. Not sure, but suspect it should also have my qualifications ( BA (Psych) & BSc (Hons) Psychology). Mobile number 0412 903 618.

```html
<!DOCTYPE html>
<html lang="en">
<head>
<meta charset="utf-8">
<title>Corvella — Business Card</title>
<link rel="stylesheet" href="https://fonts.googleapis.com/css2?family=Questrial&family=Raleway:wght@300;400;700&display=swap">
<style>
  :root {
    --backdrop: #e6ebe0;
    --card-dark: #262626;
    --card-light: #eef0f4;
    --taupe: #8a6f57;
    --taupe-deep: #6b5646;
    --slate: #4a4a47;
    --mist: #c9cbce;
    --ink: #55565a;
    --ink-soft: #7a7b80;
  }
  * { margin: 0; padding: 0; box-sizing: border-box; }
  html, body {
    width: 1200px;
    height: 797px;
    overflow: hidden;
    background: var(--backdrop);
  }
  .sheet {
    width: 1200px;
    height: 797px;
    display: flex;
    align-items: center;
    justify-content: center;
    gap: 60px;
  }
  .card {
    position: relative;
    width: 520px;
    height: 297px;
    overflow: hidden;
    box-shadow: 0 6px 18px rgba(60, 70, 55, 0.18);
  }

  /* Front */
  .card--front { background: var(--card-dark); }
  .front__band {
    position: absolute;
    top: 0;
    left: 350px;
    width: 120px;
    height: 8px;
    background: var(--taupe-deep);
  }
  .front__band-shadow {
    position: absolute;
    top: 8px;
    left: 395px;
    width: 75px;
    height: 12px;
    background: var(--slate);
  }
  .front__edge-mark {
    position: absolute;
    left: 0;
    top: 168px;
    width: 30px;
    height: 30px;
    background: var(--slate);
  }
  .front__wordmark {
    position: absolute;
    left: 56px;
    top: 158px;
    font-family: "Questrial", sans-serif;
    font-size: 46px;
    letter-spacing: 1px;
    color: var(--taupe);
  }

  /* Back */
  .card--back { background: var(--card-light); }
  .back__band {
    position: absolute;
    top: 0;
    left: 0;
    width: 215px;
    height: 16px;
    background: var(--mist);
  }
  .back__square {
    position: absolute;
    right: 0;
    top: 118px;
    width: 26px;
    height: 24px;
    background: var(--taupe-deep);
  }
  .back__web {
    position: absolute;
    right: 42px;
    top: 176px;
    font-family: "Raleway", sans-serif;
    font-weight: 400;
    font-size: 13px;
    color: var(--ink);
  }
  .back__web strong { color: var(--taupe-deep); font-weight: 700; }
  .holder {
    position: absolute;
    left: 34px;
    top: 184px;
    font-family: "Raleway", sans-serif;
    color: var(--ink);
  }
  .holder__name {
    font-weight: 300;
    font-size: 20px;
    letter-spacing: 0.5px;
    text-transform: uppercase;
  }
  .holder__quals {
    font-weight: 400;
    font-size: 11px;
    color: var(--ink-soft);
    margin-top: 2px;
  }
  .contact {
    list-style: none;
    margin-top: 16px;
    font-size: 13px;
    font-weight: 400;
    line-height: 18px;
  }
  .contact__label {
    display: inline-block;
    width: 20px;
    font-weight: 700;
    color: var(--taupe-deep);
  }
</style>
</head>
<body>
  <main class="sheet">
    <section class="card card--front" aria-label="Card front">
      <div class="front__band"></div>
      <div class="front__band-shadow"></div>
      <div class="front__edge-mark"></div>
      <div class="front__wordmark">Corvella</div>
    </section>

    <section class="card card--back" aria-label="Card back">
      <div class="back__band"></div>
      <div class="back__square"></div>
      <div class="back__web">www.<strong>corvella</strong>.com</div>
      <div class="holder">
        <h1 class="holder__name">Nel Marrick</h1>
        <p class="holder__quals">BA (Psych) &amp; BSc (Hons) Psychology</p>
        <ul class="contact">
          <li><span class="contact__label">M</span>0412 903 618</li>
          <li><span class="contact__label">E</span>n.marrick@corvella.com</li>
        </ul>
      </div>
    </section>
  </main>
</body>
</html>
```